Real Estate Website

Please refer to the attached document. It will be for a real estate agency specialising in commercial and residential sales. looking for Modern and minimalist, Sleek, professional, premium feel

```html
<!DOCTYPE html>
<html lang="en">
<head>
<meta charset="utf-8">
<title>Marlow Crest Group – Commercial & Residential Property</title>
<link href="https://fonts.googleapis.com/css2?family=Poppins:wght@400;500;600;700&display=swap" rel="stylesheet">
<style>
:root{
  --orange:#f15a29;
  --orange-soft:#f47a52;
  --navy:#27394a;
  --navy-dark:#22344a;
  --text:#2b2b2b;
  --muted:#6b6b6b;
  --grey-bg:#f3f3f2;
  --line:#e3e3e3;
  --white:#ffffff;
}
*{margin:0;padding:0;box-sizing:border-box}
html,body{width:1200px;height:5034px;overflow:hidden}
body{font-family:'Poppins',sans-serif;color:var(--text);background:var(--white);position:relative}
.abs{position:absolute}
.accent{color:var(--orange)}
.eyebrow{display:flex;align-items:center;gap:8px;font-size:12px;font-weight:600;letter-spacing:.3px;color:var(--navy);text-transform:uppercase}
.eyebrow .dot{width:14px;height:14px;border-radius:50%;border:3px solid var(--orange)}
.eyebrow.center{justify-content:center}
.title{font-size:25px;font-weight:500;color:var(--navy);line-height:1.3}
.title.center{text-align:center}
.btn{display:inline-flex;align-items:center;justify-content:center;gap:8px;font-size:13px;font-weight:500;border-radius:3px;color:var(--white)}
.btn-navy{background:var(--navy)}
.btn-orange{background:var(--orange)}
.para{font-size:12.5px;line-height:1.75;color:#555}
.photo{border-radius:2px}

/* header */
.site-header{top:0;left:0;width:1200px;height:98px;background:var(--white)}
.brand{display:flex;align-items:center;gap:10px;font-weight:700;font-size:24px;color:var(--navy)}
.brand .mark{width:26px;height:26px;border-radius:50%;background:var(--orange)}
.site-header .brand{left:94px;top:30px}
.nav{left:338px;top:38px;display:flex;gap:27px;font-size:12px;font-weight:500;color:var(--navy)}
.site-header .btn{left:981px;top:27px;width:123px;height:41px;font-size:12px}

/* hero */
.hero{top:98px;left:0;width:1200px;height:557px;background:linear-gradient(100deg,#1c2a36 0%,#2b4556 35%,#3d6b86 60%,#7fb0d4 80%,#a9c9e2 100%)}
.hero-shade{top:0;left:0;width:700px;height:557px;background:linear-gradient(90deg,rgba(10,18,26,.55),rgba(10,18,26,0))}
.hero h1{left:143px;top:102px;width:520px;font-size:38px;font-weight:700;line-height:1.33;color:var(--white)}
.hero .sub{left:143px;top:322px;width:420px;font-size:14px;line-height:1.75;color:var(--white)}
.hero .btn{left:143px;top:400px;width:182px;height:39px;font-size:12px}
.scroll-cue{left:565px;top:620px;width:70px;height:70px;border-radius:50%;background:var(--white);box-shadow:0 4px 16px rgba(0,0,0,.12);display:flex;align-items:center;justify-content:center}

/* appraisal */
.frame{left:176px;top:793px;width:344px;height:305px;border:1.5px solid var(--orange-soft)}
.photo-main{left:0;top:807px;width:508px;height:459px;background:linear-gradient(135deg,#dcd9d3,#b8b4ad 55%,#3a3f48)}
.photo-small{left:309px;top:1104px;width:250px;height:209px;background:linear-gradient(135deg,#dfe6ee,#9fb2c4);border:6px solid var(--white);box-shadow:0 6px 20px rgba(0,0,0,.12)}
.pin{left:288px;top:1081px;width:38px;height:38px;border-radius:50%;background:var(--white);box-shadow:0 2px 8px rgba(0,0,0,.15);display:flex;align-items:center;justify-content:center}
.pin span{width:16px;height:16px;border-radius:50%;border:3px solid var(--orange)}
.appraisal-text{left:602px;top:822px;width:470px}
.appraisal-text .title{margin:14px 0 14px}
.appraisal-text .para{margin-bottom:10px}
.appraisal-text .btn{width:204px;height:41px;margin-top:16px}
.city-faint{left:770px;top:1200px;width:360px;height:165px;background:linear-gradient(180deg,rgba(230,230,230,0),rgba(225,225,225,.55))}

/* services */
.services{top:1436px;left:0;width:1200px;height:606px;background:var(--grey-bg)}
.services .eyebrow{position:absolute;top:72px;width:100%}
.services .title{position:absolute;top:103px;width:100%}
.cards{position:absolute;top:162px;left:141px;display:flex;gap:33px}
.card{width:284px;height:352px;background:var(--white);border:1px solid var(--line);border-radius:3px;overflow:hidden}
.card .img{height:162px}
.card .body{padding:18px 14px}
.card h3{font-size:14px;font-weight:500;color:var(--navy);margin-bottom:8px}
.card p{font-size:12px;line-height:1.8;color:var(--muted);height:92px}
.learn{display:flex;align-items:center;gap:10px;font-size:12px;color:var(--navy);text-decoration:underline;margin-top:10px}

/* why */
.why .eyebrow{position:absolute;top:2150px;left:0;width:1200px}
.why .title{position:absolute;top:2186px;left:0;width:1200px}
.core{left:467px;top:2241px;width:266px;height:266px;border-radius:50%;background:var(--white);box-shadow:0 6px 30px rgba(0,0,0,.09);display:flex;align-items:center;justify-content:center}
.core-ring{width:232px;height:232px;border-radius:50%;border:2px dashed var(--navy);display:flex;flex-direction:column;align-items:center;justify-content:center;gap:10px}
.core-ring .mark{width:40px;height:40px;border-radius:50%;background:var(--orange)}
.core-ring .name{font-size:21px;font-weight:700;color:var(--navy)}
.feature{width:280px}
.feature h4{font-size:14px;font-weight:500;color:var(--navy);margin-bottom:6px}
.feature p{font-size:12px;line-height:1.75;color:var(--muted)}
.feature.left{text-align:right}
.ficon{width:58px;height:58px;border-radius:50%;display:flex;align-items:center;justify-content:center}
.ficon.o{background:var(--orange-soft)}
.ficon.n{background:var(--navy)}
.why .btn{left:498px;top:2554px;width:204px;height:45px}

/* about */
.about{top:2716px;left:0;width:1200px;height:528px;background:var(--grey-bg)}
.about-text{left:143px;top:2799px;width:450px}
.about-text .title{margin:12px 0 16px}
.about-text .para{margin-bottom:14px}
.about-text .btn{width:205px;height:41px;margin-top:8px}
.about-photo{left:643px;top:2796px;width:412px;height:346px;background:linear-gradient(120deg,#3a4a5a,#8ea3b6 45%,#dfe6ec);border-radius:4px}

/* testimonials */
.testi .eyebrow{position:absolute;top:3326px;left:0;width:1200px}
.testi .title{position:absolute;top:3361px;left:0;width:1200px}
.tcards{left:141px;top:3433px;display:flex;gap:33px}
.tcard{position:relative;width:284px;height:284px;background:var(--white);box-shadow:0 4px 22px rgba(0,0,0,.07);border-radius:3px;padding:38px 22px 0}
.qmark{position:absolute;left:20px;top:-14px;width:38px;height:38px;border-radius:50%;display:flex;align-items:center;justify-content:center;color:var(--white);font-size:26px;font-weight:700;line-height:1}
.qmark.n{background:var(--navy)}
.qmark.o{background:var(--orange-soft)}
.trow{display:flex;justify-content:space-between;align-items:center}
.stars{color:#f5a623;font-size:17px;letter-spacing:2px}
.gbadge{width:22px;height:22px;border-radius:50%;border:3px solid #c9c9c9}
.tcard blockquote{font-size:12px;line-height:1.85;color:#555;margin-top:20px;height:106px}
.tcard .who{margin-top:30px;font-size:13px;font-weight:500;color:var(--navy)}
.tcard .role{font-size:11.5px;color:var(--muted)}
.arrow{width:24px;height:24px;border-radius:50%;display:flex;align-items:center;justify-content:center}
.arrow.prev{left:90px;top:3564px;background:#d5d5d5}
.arrow.next{left:1086px;top:3564px;background:var(--navy)}
.dots{left:0;top:3744px;width:1200px;display:flex;justify-content:center;gap:8px}
.dots span{width:7px;height:7px;border-radius:50%;background:#d6d6d6}
.dots span.on{background:var(--orange)}

/* contact */
.contact-band{top:3830px;left:0;width:1200px;height:830px;background:linear-gradient(180deg,#f26a3d,#f47c54);clip-path:polygon(0 117px,100% 0,100% 100%,0 100%)}
.contact-card{left:141px;top:3957px;width:918px;height:537px;background:var(--white);border-radius:4px;box-shadow:0 10px 30px rgba(0,0,0,.08)}
.contact-card .eyebrow{position:absolute;top:74px;width:100%}
.contact-card .title{position:absolute;top:108px;width:100%}
.field{position:absolute;height:49px;border:1px solid #dcdcdc;border-radius:3px;display:flex;align-items:flex-start;padding:15px 16px;font-size:12px;color:#8a8a8a;gap:14px}
.field .ico{width:14px;height:14px;border:1.5px solid #b5b5b5;border-radius:3px;flex:none}
.field .sep{width:1px;height:18px;background:#ddd;margin-top:-2px}
.submit{position:absolute;left:121px;top:422px;width:676px;height:47px;background:var(--navy);color:var(--white);font-size:13px;font-weight:500;border-radius:3px;display:flex;align-items:center;justify-content:center;gap:8px}

/* footer */
.site-footer{top:4582px;left:0;width:1200px;height:452px;background:var(--navy-dark);clip-path:polygon(0 78px,100% 0,100% 100%,0 100%)}
.site-footer .brand{left:143px;top:148px;color:var(--white)}
.fdesc{left:143px;top:206px;width:220px;font-size:12px;line-height:1.75;color:#dfe4ea}
.follow{left:143px;top:304px;display:flex;align-items:center;gap:8px;font-size:12px;color:var(--white)}
.follow span.s{width:22px;height:22px;border-radius:50%;background:#f2f2f2}
.follow span.s.o{background:var(--orange)}
.fcol{top:152px;color:var(--white)}
.fcol h5{font-size:14px;font-weight:500;margin-bottom:18px}
.fcol li{list-style:none;font-size:12px;color:#dfe4ea;margin-bottom:11px}
.fcol li::before{content:"›";color:var(--orange);margin-right:6px}
.citem{display:flex;gap:16px;align-items:flex-start;font-size:12px;line-height:1.7;color:#dfe4ea;width:220px;margin-bottom:22px}
.citem .ci{width:30px;height:30px;border-radius:50%;background:#3a4d61;flex:none;display:flex;align-items:center;justify-content:center}
.citem .ci.o{background:var(--orange)}
.fline{left:0;top:400px;width:1200px;height:1px;background:rgba(255,255,255,.12)}
.copy{left:0;top:418px;width:1200px;text-align:center;font-size:11px;color:#dfe4ea}
</style>
</head>
<body>

<header class="site-header abs">
  <div class="brand abs"><span class="mark"></span>Marlow Crest Group</div>
  <nav class="nav abs">
    <span>HOME</span><span>COMMERCIAL/INDUSTRIAL</span><span>RESIDENTIAL</span><span>BUSINESS SALES</span><span>ABOUT US</span><span>INFO ⌄</span>
  </nav>
  <span class="btn btn-orange abs">CONTACT US</span>
</header>

<section class="hero abs" role="img" aria-label="Modern glass office towers beside a riverside walkway at dusk">
  <div class="hero-shade abs"></div>
  <h1 class="abs">Specialists in Commercial/ Industrial Property, Trusted in Residential Property</h1>
  <p class="sub abs">Maximising returns, protecting investments, expert property advisory</p>
  <span class="btn btn-orange abs">BOOK AN APPRAISAL</span>
</section>
<div class="scroll-cue abs">
  <svg width="16" height="16" viewBox="0 0 16 16" fill="none" stroke="#27394a" stroke-width="1.6"><path d="M4 3l4 4 4-4M4 9l4 4 4-4"/></svg>
</div>

<!-- appraisal -->
<div class="frame abs"></div>
<div class="photo-main abs photo" role="img" aria-label="Agents reviewing architectural floor plans on a desk"></div>
<div class="photo-small abs photo" role="img" aria-label="Clients shaking hands across a meeting table"></div>
<div class="pin abs"><span></span></div>
<div class="city-faint abs" role="img" aria-label="Faint city skyline line drawing"></div>
<div class="appraisal-text abs">
  <div class="eyebrow"><span class="dot"></span>Book an Appraisal</div>
  <h2 class="title">Discover The Real Value Of <span class="accent">Your Property</span></h2>
  <p class="para">At Marlow Crest Group, we don't just provide standard appraisals — we deliver strategic, insight-driven reports that uncover the true drivers of your property's worth. Whether it's commercial, industrial, or residential, our expertise ensures you see the full picture.</p>
  <p class="para">From market trends and rental potential to investment performance and future growth opportunities, our tailored reports give you clarity, confidence, and actionable insights.</p>
  <p class="para">Book a confidential consultation today and gain the expert guidance you need to maximise returns and make smarter property decisions.</p>
  <span class="btn btn-navy">Schedule Consultation
    <svg width="10" height="10" viewBox="0 0 10 10" fill="none" stroke="#fff" stroke-width="1.3"><path d="M2 8l6-6M3 2h5v5"/></svg></span>
</div>

<!-- services -->
<section class="services abs">
  <div class="eyebrow center"><span class="dot"></span>What We Do</div>
  <h2 class="title center">Property Management, <span class="accent">Sales &amp; Leasing</span></h2>
  <div class="cards">
    <article class="card">
      <div class="img" role="img" aria-label="Glass commercial office building and plaza" style="background:linear-gradient(160deg,#3e5a78,#9ab0c4 60%,#d8dde2)"></div>
      <div class="body"><h3>Commercial &amp; Industrial</h3>
        <p>Specialist management and leasing of premium commercial and industrial assets, trusted by investors and developers.</p>
        <span class="learn">Learn More <svg width="18" height="8" viewBox="0 0 18 8" fill="none" stroke="#f15a29" stroke-width="1.3"><path d="M0 4h16M13 1l3 3-3 3"/></svg></span></div>
    </article>
    <article class="card">
      <div class="img" role="img" aria-label="Two-storey brick family home with garden" style="background:linear-gradient(180deg,#5b8fcf,#a9c6e4 45%,#8a6a55 70%,#6f8e4c)"></div>
      <div class="body"><h3>Residential Property</h3>
        <p>Expert residential property management and sales services with proven results and exceptional client outcomes.</p>
        <span class="learn">Learn More <svg width="18" height="8" viewBox="0 0 18 8" fill="none" stroke="#f15a29" stroke-width="1.3"><path d="M0 4h16M13 1l3 3-3 3"/></svg></span></div>
    </article>
    <article class="card">
      <div class="img" role="img" aria-label="Advisors discussing financial reports at a laptop" style="background:linear-gradient(135deg,#cfd6dd,#7d8c99 55%,#4b5560)"></div>
      <div class="body"><h3>Property Advisory</h3>
        <p>Comprehensive financial reporting, budgeting, and expense management to optimize cash flow and returns.</p>
        <span class="learn">Learn More <svg width="18" height="8" viewBox="0 0 18 8" fill="none" stroke="#f15a29" stroke-width="1.3"><path d="M0 4h16M13 1l3 3-3 3"/></svg></span></div>
    </article>
  </div>
</section>

<!-- why -->
<section class="why">
  <div class="eyebrow center"><span class="dot"></span>Why Choose Us</div>
  <h2 class="title center">Commercial &amp; Industrial Property <span class="accent">Management &amp; Leasing</span></h2>

  <div class="feature left abs" style="left:101px;top:2262px">
    <h4>Sector Expertise</h4>
    <p>Deep knowledge across medical, healthcare, franchise, retail, and industrial sectors, enabling tailored strategies for each asset class.</p>
  </div>
  <div class="ficon o abs" style="left:399px;top:2271px">
    <svg width="26" height="26" viewBox="0 0 26 26" fill="none" stroke="#fff" stroke-width="1.6"><circle cx="13" cy="13" r="10"/><path d="M13 7.5l1.7 3.5 3.8.5-2.8 2.6.7 3.8L13 16.1l-3.4 1.8.7-3.8-2.8-2.6 3.8-.5z"/></svg>
  </div>
  <div class="feature left abs" style="left:101px;top:2425px">
    <h4>Proactive Asset Management</h4>
    <p>Beyond operations, we actively enhance value, mitigate risk, and secure the right tenants.</p>
  </div>
  <div class="ficon n abs" style="left:399px;top:2432px">
    <svg width="26" height="26" viewBox="0 0 26 26" fill="none" stroke="#fff" stroke-width="1.6"><path d="M4 14l5-5 4 2 5-4 4 4-6 7-3-2-4 4z"/></svg>
  </div>

  <div class="core abs"><div class="core-ring"><span class="mark"></span><span class="name">Marlow Crest</span></div></div>

  <div class="ficon n abs" style="left:745px;top:2271px">
    <svg width="26" height="26" viewBox="0 0 26 26" fill="none" stroke="#fff" stroke-width="1.6"><circle cx="13" cy="13" r="4"/><circle cx="13" cy="13" r="9" stroke-dasharray="4 3"/></svg>
  </div>
  <div class="feature abs" style="left:819px;top:2262px">
    <h4>Bespoke Solutions</h4>
    <p>Every property is unique. We craft customised management and leasing strategies aligned with your objectives and market conditions.</p>
  </div>
  <div class="ficon o abs" style="left:745px;top:2435px">
    <svg width="26" height="26" viewBox="0 0 26 26" fill="none" stroke="#fff" stroke-width="1.6"><path d="M5 12h4v9H5zM9 12l4-7c2 0 3 1 2.5 3L15 11h5c1.2 0 2 1 1.7 2l-1.5 6c-.3 1.2-1.2 2-2.4 2H9"/></svg>
  </div>
  <div class="feature abs" style="left:819px;top:2425px">
    <h4>Professional Excellence</h4>
    <p>Integrity, precision, and industry-leading best</p>
  </div>

  <span class="btn btn-orange abs">Book an Appraisal
    <svg width="10" height="10" viewBox="0 0 10 10" fill="none" stroke="#fff" stroke-width="1.3"><path d="M2 8l6-6M3 2h5v5"/></svg></span>
</section>

<!-- about -->
<section class="about abs"></section>
<div class="about-text abs">
  <div class="eyebrow"><span class="dot"></span>Who We Are</div>
  <h2 class="title">We Are Recognised As <span class="accent">A Trusted</span></h2>
  <p class="para">At Marlow Crest Group, we are recognised as a trusted authority in commercial and residential property management, sales, and leasing. Property owners, investors, and developers turn to us for our proven expertise, discretion, and consistent results.</p>
  <p class="para">Our mission is to set the standard for excellence in property services. Guided by innovation, integrity, and strategic execution, we deliver outcomes that protect assets, maximise returns, and create enduring value for our clients.</p>
  <span class="btn btn-navy">Schedule Consultation
    <svg width="10" height="10" viewBox="0 0 10 10" fill="none" stroke="#fff" stroke-width="1.3"><path d="M2 8l6-6M3 2h5v5"/></svg></span>
</div>
<div class="about-photo abs" role="img" aria-label="Team meeting in a bright office boardroom"></div>

<!-- testimonials -->
<section class="testi">
  <div class="eyebrow center"><span class="dot"></span>Testimonials</div>
  <h2 class="title center">What Our Clients Say <span class="accent">About Us</span></h2>
  <div class="tcards abs">
    <article class="tcard"><span class="qmark n">“</span>
      <div class="trow"><span class="stars">★★★★★</span><span class="gbadge"></span></div>
      <blockquote>"Sed ut perspiciatis unde omnis iste natus error sit voluptatem accusantium laudantium, totam rem aperiam, eaque ipsa quae ab illo inventore veritatis architect"</blockquote>
      <div class="who">Owen Harlow</div><div class="role">Asset Portfolio Manager</div>
    </article>
    <article class="tcard"><span class="qmark o">“</span>
      <div class="trow"><span class="stars">★★★★★</span><span class="gbadge"></span></div>
      <blockquote>"Sed ut perspiciatis unde omnis iste natus error sit voluptatem accusantium laudantium, totam rem aperiam, eaque ipsa quae ab illo inventore veritatis architect"</blockquote>
      <div class="who">Nadia Brooks</div><div class="role">Senior Leasing Specialist</div>
    </article>
    <article class="tcard"><span class="qmark n">“</span>
      <div class="trow"><span class="stars">★★★★★</span><span class="gbadge"></span></div>
      <blockquote>"Sed ut perspiciatis unde omnis iste natus error sit voluptatem accusantium laudantium, totam rem aperiam, eaque ipsa quae ab illo inventore veritatis architect"</blockquote>
      <div class="who">Julian Reyes</div><div class="role">Regional Property Director</div>
    </article>
  </div>
  <span class="arrow prev abs"><svg width="8" height="10" viewBox="0 0 8 10" fill="none" stroke="#fff" stroke-width="1.6"><path d="M6 1L2 5l4 4"/></svg></span>
  <span class="arrow next abs"><svg width="8" height="10" viewBox="0 0 8 10" fill="none" stroke="#fff" stroke-width="1.6"><path d="M2 1l4 4-4 4"/></svg></span>
  <div class="dots abs"><span></span><span class="on"></span><span></span><span></span></div>
</section>

<!-- contact -->
<div class="contact-band abs"></div>
<section class="contact-card abs">
  <div class="eyebrow center"><span class="dot"></span>Contact Us</div>
  <h2 class="title center">Ready To Discuss Your <span class="accent">Property Goals?</span></h2>
  <div class="field" style="left:121px;top:160px;width:330px"><span class="ico"></span><span class="sep"></span>First Name</div>
  <div class="field" style="left:467px;top:160px;width:330px"><span class="ico"></span><span class="sep"></span>Last Name</div>
  <div class="field" style="left:121px;top:224px;width:330px"><span class="ico"></span><span class="sep"></span>Your Email</div>
  <div class="field" style="left:467px;top:224px;width:330px"><span class="ico"></span><span class="sep"></span>Phone</div>
  <div class="field" style="left:121px;top:287px;width:676px;height:102px"><span class="ico"></span><span class="sep"></span>Your Message</div>
  <div class="submit">Submit Now
    <svg width="10" height="10" viewBox="0 0 10 10" fill="none" stroke="#fff" stroke-width="1.3"><path d="M2 8l6-6M3 2h5v5"/></svg></div>
</section>

<!-- footer -->
<footer class="site-footer abs">
  <div class="brand abs"><span class="mark"></span>Marlow Crest Group</div>
  <p class="fdesc abs">Sed ut perspiciatis unde omnis iste natus error sit voluptatem accusantium dolorem.</p>
  <div class="follow abs">Follow Us: <span class="s"></span><span class="s o"></span><span class="s"></span></div>
  <div class="fcol abs" style="left:416px">
    <h5>Quick Links</h5>
    <ul><li>Home</li><li>Commercial / Industrial</li><li>Residential</li><li>Business Sales ⌄</li><li>About Us</li><li>Contact us</li></ul>
  </div>
  <div class="fcol abs" style="left:651px">
    <h5>Key Offerings</h5>
    <ul><li>Business listings</li><li>Appraisal report</li><li>What we do</li><li>Who we are</li></ul>
  </div>
  <div class="fcol abs" style="left:838px">
    <h5>Contact Us</h5>
    <div class="citem"><span class="ci"><svg width="12" height="14" viewBox="0 0 12 14" fill="none" stroke="#fff" stroke-width="1.4"><path d="M6 13s4.5-4.3 4.5-7.5a4.5 4.5 0 0 0-9 0C1.5 8.7 6 13 6 13z"/><circle cx="6" cy="5.5" r="1.6"/></svg></span>123, Lorem ipsum, dolor sit amet, adipiscing elit, 45</div>
    <div class="citem"><span class="ci o"><svg width="13" height="13" viewBox="0 0 13 13" fill="#fff"><path d="M3 1l2 2.8-1.2 1.4a7 7 0 0 0 4 4L9.2 8 12 10l-1 2c-5 0-10-5-10-10z"/></svg></span><span style="margin-top:6px">Phone: (123) 456 7890</span></div>
    <div class="citem"><span class="ci"><svg width="14" height="10" viewBox="0 0 14 10" fill="none" stroke="#fff" stroke-width="1.3"><rect x="1" y="1" width="12" height="8"/><path d="M1 1l6 5 6-5"/></svg></span><span style="margin-top:6px">info@marlowcrest.example</span></div>
  </div>
  <div class="fline abs"></div>
  <p class="copy abs">© 2023 Marlow Crest Business Sales. All Rights Reserved.</p>
</footer>

</body>
</html>
```